Give Gold Kite an Online Presence!

Gold Kite Property Maintenance is an Australian Owned property maintenance company who needs a stand out online presence.

GK maintains many buildings and sites and wants to appeal to a corporate professional market with their brand new website. GK is essentially a handyman service offering all maintenance services to home owners, office managers, real estate agents and strata managers.

The Website:
We need a corporate website that appeals to our broader customer base (property owners, property managers, office managers) the copy is being written by a professional so use filler text for now.

Things that we want:
Home page that sets us apart and appeals to the corporate and residential market. The home page needs to not focus on either the residential or commercial market. The home page should focus on our logo and branding. We have a logo already and it is attached to the brief, please use it and try to consider the colour pallette that goes with it. Whilst we want the site to appear strong and manly it is important to remember that 95% of our customers are female so we need the site to be appealing to women. Women need to believe that we are strong, dependable and trustworthy.
We'd like a quote page and potentially also the ability to get a quote from the home page (please don't put it in if it ruins the overall feel of the home page)
An "about us" page
A contact us page
A blog that's built in (we don't want to link to an external blog)
(overall we'd expect to have 6 or 7 pages total)

The site will also need coding - we expect this to be done in a separate project but need you to consider a few things about the coding side of things.

It needs to be iPhone and iPad compatible.

We'd like you to suggest the best CMS that you would use or if you would suggest not using a CMS please let us know with your submissions.

Target Market(s)

Property owners, office managers and property managers who need maintenance on buildings (So all of them)

Industry/Entity Type

Property Maintenance

Requirements
Must have
• Our Logo
Home page
About Us
Residential
Commercial
Real Estate/Strata
Contact Us/Quote
Blog
Nice to have
• Quote form included in home page
Movement on the home page at least
Should not have
• other logos, too much colour
NO FLASH

```html
<!DOCTYPE html>
<html lang="en">
<head>
<meta charset="utf-8">
<title>Gold Kite Property Maintenance</title>
<link rel="stylesheet" href="https://fonts.googleapis.com/css2?family=Oswald:wght@300;400&family=Open+Sans:wght@400;600&display=swap">
<style>
:root{
  --orange:#f5841f;
  --orange-light:#f99a33;
  --orange-dark:#ee7510;
  --dark:#1f1f1f;
  --dark-2:#2c2c2c;
  --ink:#333333;
  --muted:#666666;
  --line:#e4e4e4;
  --page:#ffffff;
  --footer:#ebebeb;
  --icon:#6b6b6b;
}
*{margin:0;padding:0;box-sizing:border-box}
html,body{width:904px;height:1200px;overflow:hidden;background:var(--page)}
body{position:relative;font-family:"Open Sans",Arial,sans-serif;color:var(--ink)}
.abs{position:absolute}
.head-band{left:0;top:0;width:904px;height:358px;background:linear-gradient(180deg,var(--dark-2),var(--dark))}
.brand{left:63px;top:30px;display:flex;align-items:center;gap:6px}
.brand-mark{width:16px;height:16px;background:var(--orange)}
.brand-name{font-family:"Oswald",sans-serif;font-weight:400;font-size:19px;color:var(--orange);line-height:1.05;width:76px}
.call{right:105px;top:28px;font-family:"Open Sans",sans-serif;font-size:15.5px;color:#fff;letter-spacing:.2px}
.social-dot{width:22px;height:22px;border-radius:50%;background:#e9e9e9}
.search{left:642px;top:65px;width:218px;height:26px;background:#fff;border:1px solid #ccc;font-size:10px;color:#888;padding:6px 9px}
.search svg{position:absolute;right:6px;top:5px}
.nav{left:39px;top:103px;width:826px;height:45px;background:linear-gradient(180deg,var(--orange-light),var(--orange-dark));border-radius:3px 3px 0 0}
.nav a{position:absolute;top:0;line-height:45px;color:#fff;font-size:10.5px;text-decoration:none;transform:translateX(-50%);white-space:nowrap}
.nav i{position:absolute;top:0;width:1px;height:45px;background:rgba(255,255,255,.3)}
.hero{left:39px;top:148px;width:826px;height:300px;background:#fff}
.hero-photo{left:42px;top:148px;width:402px;height:300px;background:linear-gradient(90deg,#7fa9c7 0%,#e2b893 45%,#f3e6d8 80%,#ffffff 100%)}
.hero-copy{left:324px;top:204px;width:240px}
.hero-copy h2{font-family:"Oswald",sans-serif;font-weight:400;font-size:19px;color:#222;line-height:1.2}
.hero-copy h1{font-family:"Oswald",sans-serif;font-weight:400;font-size:24px;color:var(--orange);line-height:1.15;letter-spacing:.2px}
.hero-copy p{font-family:"Oswald",sans-serif;font-weight:300;font-size:10px;line-height:16px;color:#333;margin-top:4px;padding-left:5px}
.side{left:583px;width:281px;border-left:1px solid var(--line)}
.side-img{height:112px}
.side-cap{height:37px;background:#fff;position:relative;border-bottom:1px solid var(--line)}
.side-cap span{position:absolute;left:15px;top:8px;font-family:"Oswald",sans-serif;font-weight:300;font-size:15px;color:#444}
.side-cap svg{position:absolute;right:22px;top:6px}
.hero-shadow{left:45px;top:448px;width:814px;height:10px;background:radial-gradient(ellipse at top,rgba(0,0,0,.18),rgba(0,0,0,0) 70%)}
.card{top:472px;width:259px;height:132px;background:#fff;border:1px solid #e6e6e6;box-shadow:0 1px 3px rgba(0,0,0,.06)}
.card-img{position:absolute;right:0;top:0;width:130px;height:130px}
.card h3{position:absolute;left:19px;top:12px;font-family:"Oswald",sans-serif;font-weight:400;font-size:16px;color:#222}
.card p{position:absolute;left:19px;top:36px;width:118px;font-family:"Oswald",sans-serif;font-weight:300;font-size:9.4px;line-height:16px;color:#444}
.btn{position:absolute;left:16px;top:93px;width:71px;height:21px;background:var(--orange);color:#fff;font-size:9.6px;text-align:center;line-height:21px}
.blog{left:39px;top:632px;width:546px;height:470px;background:#fff;border:1px solid #e6e6e6;box-shadow:0 1px 3px rgba(0,0,0,.06)}
.blog-title{left:57px;top:646px;font-family:"Oswald",sans-serif;font-weight:400;font-size:18px;color:#333}
.blog-sub{left:58px;top:675px;font-family:"Oswald",sans-serif;font-weight:300;font-size:9.4px;color:#444}
.post-img{left:56px;width:133px;height:86px}
.post{left:203px;width:362px}
.post h4{font-family:"Oswald",sans-serif;font-weight:400;font-size:11.5px;color:#333;margin-bottom:4px}
.post p{font-size:9.6px;line-height:16.1px;color:#555}
.post .meta{font-family:"Oswald",sans-serif;font-weight:300;font-size:9.6px;color:#444;margin-top:3px}
.post .meta b{font-weight:300;margin:0 5px;color:#999}
.rule{left:59px;width:503px;border-top:1px dotted #c8c8c8}
.contact{left:593px;top:630px;width:274px;height:472px;background:linear-gradient(180deg,var(--orange-light),var(--orange-dark));border-radius:3px}
.contact h3{position:absolute;left:21px;top:14px;font-family:"Oswald",sans-serif;font-weight:400;font-size:18px;color:#fff}
.contact .sub{position:absolute;left:21px;top:41px;font-family:"Oswald",sans-serif;font-weight:300;font-size:9.5px;color:#fff}
.contact .div{position:absolute;left:0;top:63px;width:274px;border-top:1px solid rgba(255,255,255,.3)}
.contact label{position:absolute;left:20px;font-size:9.6px;font-weight:600;color:#fff}
.contact .field{position:absolute;left:20px;width:229px;height:25px;background:#fff;border-radius:2px}
.submit{position:absolute;left:21px;top:391px;width:63px;height:22px;background:#fbae42;color:#fff;font-size:9.8px;font-weight:600;text-align:center;line-height:22px;border-radius:2px}
.footer{left:0;top:1118px;width:904px;height:82px;background:var(--footer)}
.foot-links{left:39px;top:1136px;font-size:9.8px;color:#333}
.foot-links b{font-weight:400;color:#888;margin:0 6px}
.copy{left:39px;top:1161px;font-size:8.8px;color:#333}
.foot-dot{width:24px;height:24px;border-radius:50%;background:var(--icon)}
</style>
</head>
<body>
<div class="abs head-band"></div>

<div class="abs brand"><span class="brand-mark"></span><span class="brand-name">Gold Kite</span></div>
<div class="abs call">CALL US +61 2 5550 0142</div>
<div class="abs social-dot" style="left:811px;top:28px"></div>
<div class="abs social-dot" style="left:835px;top:28px"></div>
<div class="abs search">enter keyword
  <svg width="14" height="14" viewBox="0 0 14 14"><circle cx="5.5" cy="5.5" r="4.2" fill="none" stroke="#888" stroke-width="1.8"/><line x1="8.6" y1="8.6" x2="12.5" y2="12.5" stroke="#888" stroke-width="2"/></svg>
</div>

<nav class="abs nav">
  <a style="left:52px">HOME</a><i style="left:89px"></i>
  <a style="left:134px">ABOUT US</a><i style="left:181px"></i>
  <a style="left:233px">RESIDENTIAL</a><i style="left:284px"></i>
  <a style="left:340px">COMMERCIAL</a><i style="left:392px"></i>
  <a style="left:469px">REAL ESTATE/STRATA</a><i style="left:543px"></i>
  <a style="left:596px">CONTACT US</a><i style="left:647px"></i>
  <a style="left:683px">BLOG</a>
</nav>

<div class="abs hero"></div>
<div class="abs hero-photo" role="img" aria-label="Smiling woman in a cap giving a thumbs up, holding paint rollers and brushes"></div>
<div class="abs hero-copy">
  <h2>24/7 Services Available</h2>
  <h1>HOUSING MAINTENANCE</h1>
  <p>Mauris vel lacus vitae felis vestibulum volutpat. Etiam est nunc, venenatis in, tristique eu, imperdiet ac, nisl. Cum sociis natoque</p>
</div>

<div class="abs side" style="top:148px">
  <div class="side-img" role="img" aria-label="Woman wearing a yellow hard hat" style="background:linear-gradient(90deg,#8b7a63,#c9a77c 50%,#e7c46a)"></div>
  <div class="side-cap"><span>Ut velit enim, vestibulum non</span>
    <svg width="26" height="26" viewBox="0 0 26 26"><circle cx="13" cy="13" r="11.5" fill="none" stroke="#111" stroke-width="2"/><path d="M10.5 8.5 L17 13 L10.5 17.5Z" fill="#111"/></svg></div>
  <div style="height:2px;background:#f2f2f2"></div>
  <div class="side-img" role="img" aria-label="Woman in an orange hard hat reading plans at a work site" style="background:linear-gradient(90deg,#7b8a8c,#c07850 55%,#b8c0c2)"></div>
  <div class="side-cap" style="border-bottom:none"><span>Purus nisi eleifend libero</span>
    <svg width="26" height="26" viewBox="0 0 26 26"><circle cx="13" cy="13" r="11.5" fill="none" stroke="#111" stroke-width="2"/><path d="M10.5 8.5 L17 13 L10.5 17.5Z" fill="#111"/></svg></div>
</div>
<div class="abs hero-shadow"></div>

<div class="abs card" style="left:39px">
  <div class="card-img" role="img" aria-label="Small model house with pliers and a wrench" style="background:linear-gradient(90deg,#fff,#f1e6d8 40%,#d9d9d9)"></div>
  <h3>Featured Service</h3>
  <p>Lorem ipsum dolor sit amet, consectetuer adipiscing elit. Nam cursus.</p>
  <span class="btn">Learn More</span>
</div>
<div class="abs card" style="left:320px">
  <div class="card-img" role="img" aria-label="Tool belt with hammer and screwdrivers" style="background:linear-gradient(90deg,#fff,#caa06a 45%,#6f6a66)"></div>
  <h3>Featured Service</h3>
  <p>Lorem ipsum dolor sit amet, consectetuer adipiscing elit. Nam cursus.</p>
  <span class="btn">Learn More</span>
</div>
<div class="abs card" style="left:601px">
  <div class="card-img" role="img" aria-label="Woman in a red top drilling timber" style="background:linear-gradient(90deg,#fff,#e46a6a 50%,#e8d8b8)"></div>
  <h3>Featured Service</h3>
  <p>Lorem ipsum dolor sit amet, consectetuer adipiscing elit. Nam cursus.</p>
  <span class="btn">Learn More</span>
</div>

<div class="abs blog"></div>
<div class="abs blog-title">Recent Blog Post</div>
<div class="abs blog-sub">Lorem ipsum dolor sit amet, consectetuer adipiscing elit. Nam cursus.</div>

<div class="abs post-img" style="top:710px;background:linear-gradient(90deg,#6b4a38,#c9603a 50%,#b48a5c)" role="img" aria-label="Woman using a power drill"></div>
<div class="abs post" style="top:710px">
  <h4>Headline goes here</h4>
  <p>Duis non nunc. Nulla rhoncus dictum metus. Curabitur tristique mi condimentum orci. Phasellus pellentesque aliquam enim. Proin dui lectus, cursus eu, mattis laoreet, viverra sit amet, quam. Curabitur vel dolor ultrices ipsum dictum tristique. Praesent vitae lacus. Ut velit enim, vestibulum non, fermentum nec, hendrerit quis, leo. Pellentesque rutrum malesuada neque.</p>
  <div class="meta">Posted 2 hours ago<b>|</b>Learn More</div>
</div>
<div class="abs rule" style="top:839px"></div>

<div class="abs post-img" style="top:855px;background:linear-gradient(90deg,#3f8fd8,#d8c08a 50%,#2f86d6)" role="img" aria-label="Woman on a ladder with a paint roller"></div>
<div class="abs post" style="top:855px">
  <h4>Headline goes here</h4>
  <p>Duis non nunc. Nulla rhoncus dictum metus. Curabitur tristique mi condimentum orci. Phasellus pellentesque aliquam enim. Proin dui lectus, cursus eu, mattis laoreet, viverra sit amet, quam. Curabitur vel dolor ultrices ipsum dictum tristique.</p>
  <div class="meta">Posted 2 hours ago<b>|</b>Learn More</div>
</div>
<div class="abs rule" style="top:958px"></div>

<div class="abs post-img" style="top:975px;background:linear-gradient(90deg,#a7a6a4,#8c6a4c 50%,#b64a3a)" role="img" aria-label="Couple assembling flat-pack furniture"></div>
<div class="abs post" style="top:975px">
  <h4>Headline goes here</h4>
  <p>Duis non nunc. Nulla rhoncus dictum metus. Curabitur tristique mi condimentum orci. Phasellus pellentesque aliquam enim. Proin dui lectus, cursus eu, mattis laoreet, viverra sit amet, quam. Curabitur vel dolor ultrices ipsum dictum tristique.</p>
  <div class="meta">Posted 2 hours ago<b>|</b>Learn More</div>
</div>

<form class="abs contact">
  <h3>Fill Our Contact Form</h3>
  <div class="sub">Lorem ipsum dolor sit amet, consectetuer adipiscing</div>
  <div class="div"></div>
  <label style="top:78px">Name</label><div class="field" style="top:93px"></div>
  <label style="top:128px">Phone no.</label><div class="field" style="top:143px"></div>
  <label style="top:180px">Email address</label><div class="field" style="top:193px"></div>
  <label style="top:232px">Address</label><div class="field" style="top:245px"></div>
  <label style="top:282px">Message</label><div class="field" style="top:295px;height:85px"></div>
  <span class="submit">SUBMIT</span>
</form>

<footer class="abs footer"></footer>
<div class="abs foot-links">Home<b>|</b>About Us<b>|</b>Residential<b>|</b>Commercial<b>|</b>Real Estate/Strata<b>|</b>Contact Us<b>|</b>Blog</div>
<div class="abs copy">Copyright © 2012 Company Name. Term of Use. All right reserved</div>
<div class="abs foot-dot" style="left:804px;top:1128px"></div>
<div class="abs foot-dot" style="left:833px;top:1128px"></div>
</body>
</html>
```